CD Cover Design Project - Illustrated cover

I need a cd cover design for a new music album I am recording.

FRONT COVER:

I am not asking for a photo-montage of all the photographs provided, but an illustrated drawing. All the photographs have been attached for your reference.

I'd like the front cover to be an illustration of me playing guitar and singing into a microphone on the street in Harrowfield Yard. The illustration should have the floor made up of cobbles (see Image 1) and I'd like the building in the background to be the same as Image 2. Please keep 'Harrowfield Yard Market' written on the building, but remove 'Wren & Barrow'.

I've attached a photo of me playing guitar (Image 3) for reference.

I'd like to be illustrated wearing a dress. If you plan on showing shoes, then I'd like boots (cowgirl, etc)- my style is kind of country-chic.

I have also included a close-up of my face (Image 5). The photo is black and white so for reference, my hair is dark blonde and my eyes are hazel.

PLEASE NOTE: This black and white image is for REFERENCE ONLY. Please do not include this image on the cover as it is already being used as an album cover for my first album. It is being provided simply so you have a close up of my face and know what I look like for the drawing.

Please include my name Maribel Fenn somewhere in a prominent position.

BACK COVER:

Please make the background plain and in whatever colour you think matches the colour scheme of your front cover.

The back cover should take the following format:

List of songs in this order:

Paper Lanterns
Ring Out the Bells
Little Glass Boat
Carry Me Down the River
Silver Kite
Northbound Rain
Hollow Orchard
Dancing On a Broken Fence

www.MaribelFenn.co.uk

Hi everyone, the deadline has been extended by another 5 days. Please also take another look at the brief, as I have updated it with some extra information.

Target Market(s)

I am a street performer in London's Harrowfield Yard and my customers are made up of locals and tourists walking around the area.

Industry/Entity Type

Building

Requirements
Must have
• This cover must be an illustration / drawing.

The guitar must be acoustic.

Should not have
• The black and white photo of my face should not be used anywhere in the design. This image has been provided for reference only so you know how to draw my face.

Please do no super-impose my head from the image of me playing guitar onto the image of the dress- The angles and proportions do not match well between the two.

```html
<!DOCTYPE html>
<html lang="en">
<head>
<meta charset="utf-8">
<title>Maribel Fenn — Back Cover</title>
<link rel="stylesheet" href="https://fonts.googleapis.com/css2?family=Handlee&family=Lato:wght@400&display=swap">
<style>
  :root {
    --bg-light: #4a8c82;
    --bg-mid: #2a6e62;
    --bg-dark: #0f4a3d;
    --title-gold: #e0b54a;
    --track-cream: #ecdca4;
    --url-cream: #f2e4b4;
  }
  html, body {
    margin: 0;
    padding: 0;
    width: 1200px;
    height: 934px;
    overflow: hidden;
  }
  .back-cover {
    position: relative;
    width: 1200px;
    height: 934px;
    background: radial-gradient(ellipse 90% 95% at 50% 10%, var(--bg-light) 0%, var(--bg-mid) 50%, var(--bg-dark) 100%);
    overflow: hidden;
  }
  .artist-name {
    position: absolute;
    left: 0;
    width: 1072px;
    top: 150px;
    margin: 0;
    text-align: center;
    font-family: "Handlee", cursive;
    font-weight: 400;
    font-size: 88px;
    line-height: 1;
    color: var(--title-gold);
  }
  .track-list {
    position: absolute;
    left: 0;
    top: 345px;
    width: 1166px;
    margin: 0;
    padding: 0;
    list-style: none;
    text-align: center;
    font-family: "Handlee", cursive;
    font-size: 33px;
    line-height: 48.4px;
    color: var(--track-cream);
  }
  .website {
    position: absolute;
    left: 0;
    width: 1120px;
    top: 851px;
    margin: 0;
    text-align: center;
    font-family: "Lato", sans-serif;
    font-size: 24px;
    color: var(--url-cream);
  }
</style>
</head>
<body>
  <main class="back-cover">
    <h1 class="artist-name">Maribel Fenn</h1>
    <ol class="track-list">
      <li>Paper Lanterns</li>
      <li>Ring Out the Bells</li>
      <li>Little Glass Boat</li>
      <li>Carry Me Down the River</li>
      <li>Silver Kite</li>
      <li>Northbound Rain</li>
      <li>Hollow Orchard</li>
      <li>Dancing On a Broken Fence</li>
    </ol>
    <p class="website">www.maribelfenn.co.uk</p>
  </main>
</body>
</html>
```